Concierge Dental / Medical Supply Ordering Business - Sleek, Efficient, Professional, Elite

www.brantonkeelmedical.com - example website.

We are a concierge supply ordering business for medical and dental that provide DSO price savings on supplies while maintaining business autonomy and independence.

We want a very simple website that looks very professional says what we do and gives a very simple method to contact us & sign up as above.

Target Market(s)

Independent Dental and Medical Practices

Industry/Entity Type

Dental and Medical - healthcare

Coding

Coded - Design and coding required

Number of Pages Required

3 page

Font styles to use
Sans Serif

Colors
0054AA
0677BA
7BADD7
CADEEF
E8F1F8

Requirements
Must have
• Simple contact page, sleek efficient design, uncomplicated.
Nice to have
• Sign up page vs just a contact page.
Should not have
• Lots of pages, hard to navigate,

```html
<!DOCTYPE html>
<html lang="en">
<head>
<meta charset="utf-8">
<title>Keelpoint Dental Supply</title>
<link href="https://fonts.googleapis.com/css2?family=Poppins:wght@500;600;700&family=Lato:wght@400;700&display=swap" rel="stylesheet">
<style>
:root{
  --navy:#0054AA;
  --blue:#0677BA;
  --sky:#7BADD7;
  --mist:#CADEEF;
  --ice:#E8F1F8;
  --deep:#1A4E93;
  --ink:#1d1d1f;
  --grey:#6b6b6b;
  --black:#050505;
  --white:#fff;
}
*{box-sizing:border-box;margin:0;padding:0}
html,body{width:1200px;height:3956px;overflow:hidden}
body{font-family:"Lato",sans-serif;color:var(--ink);background:var(--white);position:relative}
h1,h2,h3,h4{font-family:"Poppins",sans-serif}
.abs{position:absolute}
.mark{width:30px;height:30px;border-radius:6px;background:linear-gradient(135deg,var(--mist),var(--blue));display:block}

.btn{display:inline-flex;align-items:center;justify-content:center;font-family:"Poppins",sans-serif;font-weight:700;font-size:15px;color:var(--white);border-radius:6px;text-transform:uppercase;background:var(--blue)}

/* header + hero */
.hero{position:absolute;left:0;top:0;width:1200px;height:685px;background:linear-gradient(160deg,#e9eef3 0%,#9fbfdc 30%,#4f8cc3 60%,#1f5fa5 100%)}
.nav{position:absolute;left:0;top:0;width:1200px;height:117px;background:rgba(40,50,60,.35)}
.nav a{position:absolute;top:48px;color:var(--white);font-size:15px;text-decoration:none}
.brand{position:absolute;left:520px;top:22px;width:160px;text-align:center;color:var(--white);font-weight:700;font-size:13px}
.brand .sq{width:52px;height:52px;border:3px solid var(--white);border-radius:8px;margin:0 auto 8px}
.login{position:absolute;left:980px;top:35px;width:109px;height:47px}
.hero-text{position:absolute;left:0;top:390px;width:1200px;text-align:center;color:var(--white)}
.hero-text .mark{width:50px;height:50px;margin:0 auto 24px;border:3px solid var(--white)}
.hero-text h1{font-size:44px;font-weight:700;margin-bottom:20px;line-height:56px}
.hero-text p{font-size:16px;margin-bottom:24px}
.order{width:135px;height:47px}

/* about */
.about-img{left:140px;top:813px;width:368px;height:368px;border-radius:60px;background:linear-gradient(135deg,#d9e3ec,#8fb3d4 55%,#2f74b8)}
.about-copy{left:628px;top:772px;width:440px}
.about-copy h2{font-size:31px;font-weight:600;margin:14px 0 28px;white-space:nowrap}
.about-copy p{font-size:15px;line-height:27.5px;color:#444}
.learn{width:135px;height:47px;margin-top:34px}

/* practice */
.practice{left:0;top:1263px;width:1200px;height:636px;background:linear-gradient(180deg,#234f8f,var(--deep))}
.practice h2{position:absolute;top:100px;width:1200px;text-align:center;color:var(--white);font-size:30px;font-weight:600}
.card{position:absolute;top:235px;width:308px;height:310px;border:2px solid var(--white);border-radius:20px;text-align:center;color:var(--white);padding:0 18px}
.card.on{background:var(--sky);border-color:var(--sky)}
.card h3{font-size:26px;font-weight:600;margin-top:88px;margin-bottom:18px;white-space:nowrap;line-height:36px}
.card p{font-size:15px;line-height:26px;padding:0 12px}
.card .ic{position:absolute;left:92px;top:-46px;width:120px;height:100px;background:var(--sky);display:flex;align-items:center;justify-content:center}
.card.on .ic{background:var(--white)}
.card .dn{position:absolute;left:142px;bottom:20px}

/* testimonials */
.center-title{width:1200px;text-align:center;font-size:30px;font-weight:600}
.quote{position:absolute;top:2115px;width:290px;text-align:center}
.quote svg{display:block;margin:0 auto}
.quote p{font-size:14px;line-height:24px;color:#555;margin-top:22px}
.quote h4{font-size:14px;font-weight:600;margin-top:20px}

/* newsletter */
.news{left:0;top:2367px;width:1200px;height:462px;background:linear-gradient(90deg,#a9d3ec 0%,#8cc4e6 60%,#6fb2de 100%)}
.tooth{left:820px;top:0;width:380px;height:462px;background:radial-gradient(ellipse at 35% 50%,#f3f6f8 0%,#d5e4ee 25%,rgba(140,196,230,0) 55%)}
.news h2{position:absolute;left:110px;top:148px;font-size:31px;font-weight:600}
.field{position:absolute;top:226px;width:302px;height:50px;background:var(--white);border:1px solid var(--mist);border-radius:25px;padding-left:30px;font-size:15px;line-height:48px;color:#333}
.signup{position:absolute;left:115px;top:306px;width:123px;height:49px;background:linear-gradient(90deg,var(--blue),#4a5a9a)}

/* blog */
.post{position:absolute;top:3034px;width:311px;height:477px;background:var(--white);box-shadow:0 2px 10px rgba(0,0,0,.1);border-bottom:3px solid var(--navy)}
.post .ph{height:212px}
.post .body{padding:30px 28px}
.post .date{font-size:14px;color:#777;display:flex;align-items:center;gap:10px}
.post h3{font-size:20px;font-weight:500;line-height:31px;margin:14px 0 12px}
.post p{font-size:15px;line-height:24px;color:#888}
.post a{display:inline-block;margin-top:8px;color:var(--blue);font-size:15px;text-decoration:underline}

/* footer */
.footer{left:0;top:3599px;width:1200px;height:357px;background:var(--black);color:var(--white)}
.footer .fname{position:absolute;left:110px;top:112px;font-weight:700;font-size:14px}
.footer .fsq{position:absolute;left:130px;top:44px;width:70px;height:60px;border:3px solid #ccc;border-radius:8px}
.social{position:absolute;top:194px;display:flex;gap:6px;left:110px}
.social span{width:38px;height:38px;border-radius:50%;background:var(--white);display:block}
.social span:first-child{background:var(--sky)}
.vline{position:absolute;left:363px;top:86px;width:1px;height:210px;background:#333}
.fcol{position:absolute;top:65px}
.fcol h4{font-size:21px;font-weight:600;margin-bottom:14px}
.fcol li{list-style:none;font-size:15px;line-height:26px}
.fcol li::before{content:"»";margin-right:12px}
.contact div{font-size:15px;line-height:24px;display:flex;gap:10px;margin-bottom:16px}
.copy{position:absolute;top:302px;width:1200px;text-align:center;font-size:15px;border-top:1px solid #222;padding-top:10px}
</style>
</head>
<body>

<section class="hero" role="img" aria-label="Photo of a smiling patient receiving a dental exam from gloved hands">
  <nav class="nav">
    <a style="left:113px">Home</a>
    <a style="left:195px">About Us</a>
    <a style="left:299px">Services</a>
    <a style="left:396px">Dental Supply</a>
    <a style="left:724px">Blog</a>
    <a style="left:795px">Contact Us</a>
    <svg class="abs" style="left:925px;top:49px" width="18" height="18" viewBox="0 0 18 18"><circle cx="7.5" cy="7.5" r="5.5" fill="none" stroke="#0e9ce0" stroke-width="2.5"/><path d="M11.5 11.5L16 16" stroke="#0e9ce0" stroke-width="2.5"/></svg>
    <div class="brand"><div class="sq"></div>Keelpoint Dental Supply</div>
    <span class="btn login">Log in</span>
  </nav>
  <svg class="abs" style="left:58px;top:360px" width="40" height="64" viewBox="0 0 40 64"><path d="M34 4L8 32l26 28" fill="none" stroke="rgba(255,255,255,.45)" stroke-width="6"/></svg>
  <svg class="abs" style="left:1103px;top:360px" width="40" height="64" viewBox="0 0 40 64"><path d="M6 4l26 28L6 60" fill="none" stroke="#fff" stroke-width="6"/></svg>
  <div class="hero-text">
    <span class="mark"></span>
    <h1>A Dental Supply &amp; Medical Consulting</h1>
    <p>Lorem ipsum dolor sit amet, consectetur adipiscing elit, sed do eiusmod tempor incididunt</p>
    <span class="btn order">Order Now</span>
  </div>
</section>

<div class="abs about-img" role="img" aria-label="Photo of a doctor and a dental nurse reviewing notes together"></div>
<div class="abs about-copy">
  <span class="mark"></span>
  <h2>About Keelpoint Dental Supply</h2>
  <p>Lorem ipsum dolor sit amet, consectetur adipiscing elit, sed do eiusmod tempor incididunt ut labore et dolore magna aliqua. Ut enim ad minim veniam, quis nostrud exercitation ullamco laboris nisi ut aliquip ex ea commodo consequat. Duis aute irure dolor in reprehenderit in voluptate velit esse cillum dolore eu fugiat nulla pariatur. Excepteur sint occaecat cupidatat non proident, sunt in culpa qui officia deserunt mollit anim id est laborum.</p>
  <span class="btn learn">Learn More</span>
</div>

<section class="abs practice">
  <span class="mark abs" style="left:585px;top:68px"></span>
  <h2>Our Practice Areas</h2>
  <div class="card" style="left:110px">
    <div class="ic"><svg width="60" height="60" viewBox="0 0 60 60" fill="none" stroke="#fff" stroke-width="2.5"><circle cx="30" cy="30" r="12"/><path d="M30 4v14M30 42v14M4 30h14M42 30h14M12 12l10 10M38 38l10 10M48 12L38 22M22 38L12 48"/></svg></div>
    <h3>Distribution</h3>
    <p>Lorem ipsum dolor sit amet, consectetur adipiscing elit, sed do eiusmod tempor incididunt ut labore et dolore magna aliqua.</p>
    <svg class="dn" width="22" height="22" viewBox="0 0 22 22"><circle cx="11" cy="11" r="11" fill="#7BADD7"/><path d="M6 9l5 5 5-5" stroke="#fff" stroke-width="2.5" fill="none"/></svg>
  </div>
  <div class="card on" style="left:447px">
    <div class="ic"><svg width="64" height="60" viewBox="0 0 64 60" fill="none" stroke="#0054AA" stroke-width="2.5"><path d="M8 4h18v10c0 8-9 12-9 12S8 22 8 14z"/><path d="M17 9v8M13 13h8"/><rect x="36" y="24" width="20" height="30" rx="3"/><rect x="38" y="18" width="16" height="6"/><path d="M46 33v12M40 39h12"/><rect x="4" y="40" width="28" height="12" rx="6" transform="rotate(-30 18 46)"/></svg></div>
    <h3>Pharma</h3>
    <p>Lorem ipsum dolor sit amet, consectetur adipiscing elit, sed do eiusmod tempor incididunt ut labore et dolore magna aliqua.</p>
    <svg class="dn" width="22" height="22" viewBox="0 0 22 22"><circle cx="11" cy="11" r="11" fill="#fff"/><path d="M6 9l5 5 5-5" stroke="#7BADD7" stroke-width="2.5" fill="none"/></svg>
  </div>
  <div class="card" style="left:782px">
    <div class="ic"><svg width="60" height="60" viewBox="0 0 60 60" fill="none" stroke="#fff" stroke-width="2.5"><rect x="6" y="4" width="8" height="52" rx="4"/><rect x="20" y="4" width="8" height="52" rx="4"/><path d="M38 56V30c0-10 6-14 6-26M52 56V30c0-10-6-14-6-26"/></svg></div>
    <h3>Capital Equipment</h3>
    <p>Lorem ipsum dolor sit amet, consectetur adipiscing elit, sed do eiusmod tempor incididunt ut labore et dolore magna aliqua.</p>
    <svg class="dn" width="22" height="22" viewBox="0 0 22 22"><circle cx="11" cy="11" r="11" fill="#7BADD7"/><path d="M6 9l5 5 5-5" stroke="#fff" stroke-width="2.5" fill="none"/></svg>
  </div>
</section>

<span class="mark abs" style="left:585px;top:1985px"></span>
<h2 class="abs center-title" style="top:2020px">What Our Clients Say</h2>
<div class="quote" style="left:107px"><svg width="54" height="44" viewBox="0 0 54 44" fill="#7BADD7"><path d="M12 16a10 10 0 1 1-10 12C2 16 10 6 20 2l2 4c-6 3-9 6-10 10z"/><path d="M40 16a10 10 0 1 1-10 12C30 16 38 6 48 2l2 4c-6 3-9 6-10 10z"/></svg><p>Loremipsumjidolorkgiusitamet, consectetur adipiscelit,seddoeiusmod temporincididunt ut labore et dolore magna aliqua.</p><h4>- JOHN DOE</h4></div>
<div class="quote" style="left:455px"><svg width="54" height="44" viewBox="0 0 54 44" fill="#7BADD7"><path d="M12 16a10 10 0 1 1-10 12C2 16 10 6 20 2l2 4c-6 3-9 6-10 10z"/><path d="M40 16a10 10 0 1 1-10 12C30 16 38 6 48 2l2 4c-6 3-9 6-10 10z"/></svg><p>Loremipsumjidolorgiusitamet, consectetur adipiscelit,seddoeiusmod temporincididunt ut labore et dolore magna aliqua.</p><h4>- JOHN DOE</h4></div>
<div class="quote" style="left:803px"><svg width="54" height="44" viewBox="0 0 54 44" fill="#7BADD7"><path d="M12 16a10 10 0 1 1-10 12C2 16 10 6 20 2l2 4c-6 3-9 6-10 10z"/><path d="M40 16a10 10 0 1 1-10 12C30 16 38 6 48 2l2 4c-6 3-9 6-10 10z"/></svg><p>Loremipsumjidolorgiusitamet, consectetur adipiscelit,seddoeiusmod temporincididunt ut labore et dolore magna aliqua.</p><h4>- JOHN DOE</h4></div>

<section class="abs news">
  <div class="abs tooth" role="img" aria-label="Photo of a white tooth model beside dental tools on a blue cloth"></div>
  <span class="mark abs" style="left:112px;top:110px"></span>
  <h2>Subscribe Newsletter</h2>
  <div class="field" style="left:110px">Name</div>
  <div class="field" style="left:430px">Email</div>
  <span class="btn signup">Sign Up</span>
</section>

<span class="mark abs" style="left:585px;top:2917px"></span>
<h2 class="abs center-title" style="top:2952px">Our Blog</h2>
<article class="post" style="left:110px">
  <div class="ph" role="img" aria-label="Photo of a smiling patient at a dental checkup" style="background:linear-gradient(135deg,#e6eef4,#b9cfe2 60%,#3c7cc0)"></div>
  <div class="body"><div class="date"><svg width="18" height="18" viewBox="0 0 18 18"><circle cx="9" cy="9" r="7.5" fill="none" stroke="#7BADD7" stroke-width="2"/><path d="M9 5v4l3 2" stroke="#7BADD7" stroke-width="2" fill="none"/></svg>December 20,2021</div>
  <h3>Sed ut perspiciatis unde omnis iste natus</h3><p>Lorem ipsum dolor sit amet, elit, sed do eiusmod tempor incididunt ut labore et dolore magna aliqua.</p><a>Learn More</a></div>
</article>
<article class="post" style="left:444px">
  <div class="ph" role="img" aria-label="Photo of a dentist explaining a teeth model at a desk" style="background:linear-gradient(135deg,#f1f3f5,#cfdbe6 55%,#5d8fc2)"></div>
  <div class="body"><div class="date"><svg width="18" height="18" viewBox="0 0 18 18"><circle cx="9" cy="9" r="7.5" fill="none" stroke="#7BADD7" stroke-width="2"/><path d="M9 5v4l3 2" stroke="#7BADD7" stroke-width="2" fill="none"/></svg>December 20,2021</div>
  <h3>Sed ut perspiciatis unde omnis iste natus</h3><p>Lorem ipsum dolor sit amet, elit, sed do eiusmod tempor incididunt ut labore et dolore magna aliqua.</p><a>Learn More</a></div>
</article>
<article class="post" style="left:777px">
  <div class="ph" role="img" aria-label="Photo of a dentist treating a patient in the chair" style="background:linear-gradient(135deg,#dfe7ee,#8aa9c9 50%,#3f4f8c)"></div>
  <div class="body"><div class="date"><svg width="18" height="18" viewBox="0 0 18 18"><circle cx="9" cy="9" r="7.5" fill="none" stroke="#7BADD7" stroke-width="2"/><path d="M9 5v4l3 2" stroke="#7BADD7" stroke-width="2" fill="none"/></svg>December 20,2021</div>
  <h3>Sed ut perspiciatis unde omnis iste natus</h3><p>Lorem ipsum dolor sit amet, elit, sed do eiusmod tempor incididunt ut labore et dolore magna aliqua.</p><a>Learn More</a></div>
</article>

<footer class="abs footer">
  <div class="fsq"></div>
  <div class="fname">Keelpoint Dental Supply</div>
  <div class="social"><span></span><span></span><span></span><span></span></div>
  <div class="vline"></div>
  <div class="fcol" style="left:421px"><h4>Quick Links</h4><ul><li>Home</li><li>About Us</li><li>Services</li><li>Dental Supply</li><li>Blog</li><li>Contact Us</li></ul></div>
  <div class="fcol" style="left:628px"><h4>Our Company</h4><ul><li>Terms &amp; Conditions</li><li>Privacy Policy</li><li>About Us</li><li>Support</li></ul></div>
  <div class="fcol contact" style="left:854px"><h4>Contact us</h4>
    <div><svg width="14" height="20" viewBox="0 0 14 20"><path d="M7 0a7 7 0 0 0-7 7c0 5 7 13 7 13s7-8 7-13a7 7 0 0 0-7-7z" fill="#fff"/><circle cx="7" cy="7" r="2.5" fill="#050505"/></svg><span>Lorem ipsum dolor sit<br>amet, consectetur adipiscing</span></div>
    <div><svg width="16" height="16" viewBox="0 0 16 16"><path d="M3 1l3 3-2 2c1 3 3 5 6 6l2-2 3 3-2 2C7 15 1 9 1 3z" fill="#fff"/></svg><span>1+ (555) 014 2290</span></div>
    <div><svg width="17" height="13" viewBox="0 0 17 13"><rect width="17" height="13" rx="1.5" fill="#fff"/><path d="M1 1l7.5 6L16 1" stroke="#050505" stroke-width="1.5" fill="none"/></svg><span>info@keelpointdental.com</span></div>
  </div>
  <div class="copy">©Copyrights 2023 Keelpoint Dental Supply &nbsp;|&nbsp; All Rights Reserved</div>
</footer>

</body>
</html>
```